Business Cards for Internet Security Company

Awesome designers! This is the opportunity to help design cards for a forward thinking network security company. They use threat information gathered from peer groups to make intelligent decisions on what threats are relevant and which arent. ( not that you need this to do designs, but just so you know where they are coming from. ) :-)

We'd like to see a two side design and the deliverables will be in illustrator 4. The logo is attached and the logo colors are attached in the JPG and I've attached a an eps of the logo and icon

Security

```html
<!DOCTYPE html>
<html lang="en">
<head>
<meta charset="utf-8">
<title>Keystrand Business Cards</title>
<link rel="stylesheet" href="https://fonts.googleapis.com/css2?family=Open+Sans:wght@400;600;700&display=swap">
<style>
  :root {
    --backdrop: #eceef2;
    --card: #fbfbfc;
    --brand-blue: #1c5aa3;
    --brand-sky: #3d97df;
    --rule-grey: #9aa0a8;
    --ink: #333840;
    --ink-soft: #555b63;
  }
  * { box-sizing: border-box; margin: 0; padding: 0; }
  html, body { width: 1200px; height: 976px; overflow: hidden; }
  body {
    background: var(--backdrop);
    font-family: "Open Sans", Arial, sans-serif;
    position: relative;
  }
  .card {
    position: absolute;
    left: 215px;
    width: 770px;
    height: 440px;
    background: var(--card);
    border-radius: 26px;
    box-shadow: 0 6px 22px rgba(40, 50, 70, 0.14);
    overflow: hidden;
  }
  .card--back { top: 30px; }
  .card--front { top: 506px; }

  .band-rule {
    position: absolute;
    left: 0; right: 0;
    height: 5px;
    background: var(--brand-blue);
  }
  .band-rule__knot {
    position: absolute;
    width: 18px; height: 18px;
    top: -6.5px;
    background: var(--brand-blue);
  }

  .wordmark {
    position: absolute;
    display: flex;
    align-items: center;
    color: var(--brand-blue);
    font-weight: 700;
    letter-spacing: -1px;
    line-height: 1;
  }
  .wordmark__dot {
    border-radius: 50%;
    background: var(--brand-sky);
    flex: none;
  }

  .card--back .wordmark {
    left: 0; right: 0; top: 120px;
    justify-content: center;
    font-size: 88px; gap: 16px;
  }
  .card--back .wordmark__dot { width: 40px; height: 40px; }
  .card--back .band-rule { top: 262px; }
  .card--back .band-rule__knot { left: 376px; }

  .card--front .wordmark { left: 48px; top: 120px; font-size: 62px; gap: 12px; }
  .card--front .wordmark__dot { width: 30px; height: 30px; }
  .card--front .band-rule { top: 300px; }
  .card--front .band-rule__knot { left: 236px; }

  .address {
    position: absolute;
    left: 48px; top: 334px;
    font-size: 20px;
    color: var(--ink);
  }

  .contact-block {
    position: absolute;
    left: 470px; top: 52px;
    width: 270px; height: 222px;
    border-left: 3px solid var(--rule-grey);
    padding-left: 26px;
  }
  .person__name {
    font-size: 22px;
    font-weight: 700;
    color: var(--ink);
    letter-spacing: 0.5px;
    line-height: 30px;
  }
  .person__role {
    font-size: 18px;
    color: var(--ink-soft);
    line-height: 26px;
    margin-bottom: 14px;
  }
  .contact-list { list-style: none; }
  .contact-list li {
    position: relative;
    font-size: 17px;
    color: var(--ink);
    line-height: 33px;
  }
  .contact-list li::before {
    content: "";
    position: absolute;
    left: -37px; top: 10px;
    width: 14px; height: 14px;
    background: var(--brand-blue);
  }
</style>
</head>
<body>
  <section class="card card--back" aria-label="Card back">
    <div class="wordmark"><span class="wordmark__dot"></span>Keystrand</div>
    <div class="band-rule"><span class="band-rule__knot"></span></div>
  </section>

  <section class="card card--front" aria-label="Card front">
    <div class="wordmark"><span class="wordmark__dot"></span>Keystrand</div>

    <div class="contact-block">
      <p class="person__name">DANIEL MARSH</p>
      <p class="person__role">Managing Director</p>
      <ul class="contact-list">
        <li>014 552 7301</li>
        <li>014 552 7302</li>
        <li>hello@keystrand.net</li>
        <li>keystrand.net</li>
      </ul>
    </div>

    <div class="band-rule"><span class="band-rule__knot"></span></div>
    <p class="address">Harlow Park, 118 Linden St. Marby</p>
  </section>
</body>
</html>
```